Corvane Holdings , new business card design

investment firm with corporate clients . need double sided business card , vertical and horizontal options ,logo must be clear. prefer pantone colors only and sharp design. website also www.corvane.ae

Khalid Bin Tarrafi
Managing Director
Tel. +971 4 387 2940
Mobile +971 50 518 2403
khalid@corvane.ae
Q-Span Plaza, officw 18-B07, Warqa Gardens, Dubai

Contact Information for Business Card

Khalid Bin Tarrafi
Managing Director

Font styles to use
Serif

Colors

Designer to choose colors to be used in the design.

```html
<!DOCTYPE html>
<html lang="en">
<head>
<meta charset="utf-8">
<title>Corvane Holdings — Business Card</title>
<link rel="stylesheet" href="https://fonts.googleapis.com/css2?family=Lato:wght@300;400;700&display=swap">
<style>
  :root {
    --stage: #e9e7e4;
    --card-dark: #0a0c11;
    --card-light: #ffffff;
    --ink: #15171c;
    --ink-soft: #2b2e35;
    --navy: #0f2160;
    --steel: #4f7aa3;
    --white: #ffffff;
  }
  * { box-sizing: border-box; margin: 0; padding: 0; }
  html, body {
    width: 1200px; height: 960px; overflow: hidden;
    background: var(--stage);
    font-family: "Lato", Arial, sans-serif;
  }
  .canvas { position: relative; width: 1200px; height: 960px; }

  .card {
    position: absolute; left: 300px; width: 600px; height: 343px;
    box-shadow: 0 6px 18px rgba(0,0,0,0.18);
  }
  .card--back { top: 80px; background: var(--card-dark); }
  .card--front { top: 510px; background: var(--card-light); }

  .wordmark {
    display: flex; align-items: center; gap: 14px;
    font-weight: 300; letter-spacing: 0.22em; text-transform: uppercase;
    line-height: 1; white-space: nowrap;
  }
  .wordmark__square { width: 14px; height: 14px; background: var(--steel); flex: none; }
  .wordmark__name { font-size: 34px; }

  .card--back .wordmark {
    position: absolute; top: 118px; left: 0; right: 0; justify-content: center;
    color: var(--white);
  }
  .card--back .website {
    position: absolute; top: 200px; left: 0; right: 0; text-align: center;
    color: var(--white); font-size: 19px; letter-spacing: 0.16em; font-weight: 400;
  }

  .card--front .wordmark {
    position: absolute; top: 46px; left: 30px; color: var(--ink);
  }

  .namebox {
    position: absolute; right: 0; top: 128px; width: 230px; height: 60px;
    background: var(--navy); color: var(--white);
    display: flex; flex-direction: column; justify-content: center;
    padding-left: 22px; padding-right: 14px; text-align: right;
  }
  .namebox__name { font-weight: 700; font-size: 14px; letter-spacing: 0.02em; text-transform: uppercase; }
  .namebox__title { font-weight: 400; font-size: 14px; letter-spacing: 0.03em; text-transform: uppercase; margin-top: 3px; }

  .contacts {
    position: absolute; left: 30px; top: 176px; list-style: none;
    color: var(--ink-soft); font-size: 14.5px; line-height: 21px;
  }
  .contacts__item { display: flex; align-items: center; gap: 7px; height: 21px; }
  .contacts__icon { width: 12px; height: 12px; flex: none; }

  .address {
    position: absolute; left: 30px; top: 268px;
    color: var(--ink-soft); font-size: 14.5px; line-height: 21px; font-style: normal;
  }
</style>
</head>
<body>
<main class="canvas">

  <section class="card card--back" aria-label="Card back">
    <div class="wordmark">
      <span class="wordmark__square"></span>
      <span class="wordmark__name">Corvane Holdings</span>
    </div>
    <p class="website">www.corvane.ae</p>
  </section>

  <section class="card card--front" aria-label="Card front">
    <div class="wordmark">
      <span class="wordmark__square"></span>
      <span class="wordmark__name">Corvane Holdings</span>
    </div>

    <div class="namebox">
      <span class="namebox__name">Khalid Bin Tarrafi</span>
      <span class="namebox__title">Managing Director</span>
    </div>

    <ul class="contacts">
      <li class="contacts__item">
        <svg class="contacts__icon" viewBox="0 0 12 12" aria-hidden="true"><circle cx="6" cy="6" r="5.5" fill="var(--navy)"/><path d="M4 3.2c.5-.3.9 0 1.1.5l.3.8c.1.3 0 .5-.3.7l-.3.2c.3.7.8 1.2 1.5 1.5l.2-.3c.2-.3.4-.4.7-.3l.8.3c.5.2.8.6.5 1.1-.4.8-1.3 1-2.1.6C5 7.7 4.3 7 3.7 5.7 3.3 4.7 3.4 3.7 4 3.2z" fill="var(--white)"/></svg>
        <span>+971 4 387 2940</span>
      </li>
      <li class="contacts__item">
        <svg class="contacts__icon" viewBox="0 0 12 12" aria-hidden="true"><rect x="3" y="0.5" width="6.5" height="11" rx="1" fill="var(--navy)"/><rect x="4" y="2" width="4.5" height="4" fill="var(--white)"/><rect x="4.2" y="7.3" width="4" height="3" fill="var(--white)" opacity=".6"/></svg>
        <span>+971 50 518 2403</span>
      </li>
      <li class="contacts__item">
        <svg class="contacts__icon" viewBox="0 0 12 12" aria-hidden="true"><rect x="0.5" y="2.5" width="11" height="7.5" rx="1" fill="var(--navy)"/><path d="M1 3.2 6 7l5-3.8" fill="none" stroke="var(--white)" stroke-width="1"/></svg>
        <span>khalid@corvane.ae</span>
      </li>
      <li class="contacts__item">
        <svg class="contacts__icon" viewBox="0 0 12 12" aria-hidden="true"><circle cx="6" cy="6" r="5.3" fill="none" stroke="var(--navy)" stroke-width="1.2"/><ellipse cx="6" cy="6" rx="2.3" ry="5.3" fill="none" stroke="var(--navy)" stroke-width="1"/><path d="M0.8 6h10.4M1.8 3.3h8.4M1.8 8.7h8.4" stroke="var(--navy)" stroke-width="0.9"/></svg>
        <span>www.corvane.ae</span>
      </li>
    </ul>

    <address class="address">
      Q-Span Plaza, officw 18-B07<br>
      Warqa Gardens, Dubai
    </address>
  </section>

</main>
</body>
</html>
```